Velvet Pressings Techno Label Business Card

I'm looking for a very clean business card for my Velvet Pressings music label. The label focusses on techno music. The card should include:

• my name : Tomas Brandt as "Founder & CEO"
• email address: tomas@velvet-pressings.example
• web: www.velvet-pressings.example
• facebook logo + /velvetpress
• twitter logo + /velvetpress
• soundcloud logo + /velvetpressings

Feel free to include your ideas! I'm looking forward to discuss about it.

Tomas

Industry/Entity Type

Business

Contact Information for Business Card

I don't like glossy cards. Prefer matt.

Requirements
Nice to have
• Maybe on one side the complete logo, other side just the icon.
Should not have
• Flashy stuff. Must be clean and business like style.

```html
<!DOCTYPE html>
<html lang="en">
<head>
<meta charset="utf-8">
<title>Velvet Pressings – Business Card</title>
<link href="https://fonts.googleapis.com/css2?family=Open+Sans:wght@400;700&display=swap" rel="stylesheet">
<style>
  :root {
    --backdrop: #ececec;
    --card: #292524;
    --card-edge: #1f1b1a;
    --accent: #ec7d1c;
    --muted: #8e8a88;
    --text-light: #b9b5b3;
  }
  * { box-sizing: border-box; margin: 0; padding: 0; }
  html, body {
    width: 1200px; height: 726px; overflow: hidden;
    background: var(--backdrop);
    font-family: "Open Sans", Arial, sans-serif;
  }
  .canvas { position: relative; width: 1200px; height: 726px; }

  .card {
    position: absolute;
    width: 540px; height: 309px;
    background: var(--card);
    border: 1px solid var(--card-edge);
    box-shadow: 0 6px 18px rgba(0,0,0,.18);
  }
  .card--front { left: 40px; top: 150px; }
  .card--back  { left: 620px; top: 267px; }

  /* Front: label name */
  .wordmark {
    position: absolute; left: 0; right: 0; top: 50%;
    transform: translateY(-50%);
    display: flex; align-items: center; justify-content: center; gap: 14px;
  }
  .wordmark__square {
    width: 22px; height: 22px; background: var(--accent); flex: none;
  }
  .wordmark__name {
    color: var(--accent); font-weight: 700; font-size: 36px; letter-spacing: -0.5px;
    white-space: nowrap;
  }

  /* Back: label name + details */
  .label-name {
    position: absolute; left: 44px; top: 176px;
    color: var(--accent); font-weight: 700; font-size: 20px; white-space: nowrap;
  }
  .person { position: absolute; left: 285px; top: 90px; }
  .person__name { color: var(--accent); font-size: 15px; letter-spacing: .5px; }
  .person__role { color: var(--muted); font-size: 9.5px; margin-top: 2px; }

  .contacts { position: absolute; left: 285px; top: 168px; list-style: none; }
  .contacts li {
    display: flex; align-items: center; gap: 8px;
    color: var(--text-light); font-size: 11px; line-height: 18px; white-space: nowrap;
  }
  .contacts svg { width: 9px; height: 9px; flex: none; }
  .icon-square { width: 9px; height: 9px; background: var(--accent); flex: none; border-radius: 1px; }
</style>
</head>
<body>
<main class="canvas">
  <section class="card card--front" aria-label="Card front">
    <div class="wordmark">
      <span class="wordmark__square" aria-hidden="true"></span>
      <span class="wordmark__name">Velvet Pressings</span>
    </div>
  </section>

  <section class="card card--back" aria-label="Card back">
    <p class="label-name">Velvet Pressings</p>
    <div class="person">
      <p class="person__name">Tomas Brandt</p>
      <p class="person__role">Founder &amp; CEO</p>
    </div>
    <ul class="contacts">
      <li>
        <svg viewBox="0 0 10 10" aria-hidden="true"><rect x="0" y="1.5" width="10" height="7" fill="var(--accent)"/><path d="M0 1.5 L5 5.5 L10 1.5" stroke="var(--card)" stroke-width="1" fill="none"/></svg>
        tomas@velvet-pressings.example
      </li>
      <li>
        <svg viewBox="0 0 10 10" aria-hidden="true"><circle cx="5" cy="5" r="4.2" fill="none" stroke="var(--accent)" stroke-width="1.4"/><path d="M0.8 5 H9.2 M5 0.8 V9.2" stroke="var(--accent)" stroke-width="1"/></svg>
        www.velvet-pressings.example
      </li>
      <li><span class="icon-square"></span>/velvetpress</li>
      <li><span class="icon-square"></span>/velvetpress</li>
      <li><span class="icon-square"></span>/velvetpressings</li>
    </ul>
  </section>
</main>
</body>
</html>
```